need corporate, modern business card created for Consulting Company

I need a slick business card using elements from my website, as well as, integrating my pixelforge-created logo (see files).

The business card needs to be:
1. Corporate and modern
2. Clean and professional

I've included a PSD with the logo/icon that you can use to create it. Feel free to try a metallic finish on the logo, make it bigger/small, underlay it. Whatever you need to do to make my card stand out.

Try a black background, or white background or gray.

The idea is for my card to be memorable as well as professional and corporate.

Target Market(s)

Corporate business in the US and Canada.

Industry/Entity Type

Business

Contact Information for Business Card

Commerce Advancing Methods
Martin Coles, Senior Partner
office: 1 877 555 0143
mobile: 1 519 555 0172
website: http://www.brightvale.example

Requirements
Must have
• Card-related information
• corporate, yet modern
• clean and professional
• incorporate the icon only
• must have an editable form when complete!
Nice to have
• metallic icon might be cool
• try it with white or black

```html
<!DOCTYPE html>
<html lang="en">
<head>
<meta charset="utf-8">
<title>Brightvale Business Card</title>
<link href="https://fonts.googleapis.com/css2?family=Open+Sans:wght@400;600;700&display=swap" rel="stylesheet">
<style>
  :root {
    --stage: #e4e5e7;
    --ink-dark: #1d1d1f;
    --ink-mid: #3b3b3e;
    --band-light: #f3f4f5;
    --brand-blue: #3d8fd1;
    --blue-deep: #1f5fa5;
    --blue-bright: #3c92d3;
    --text-light: #ffffff;
    --text-dark: #3a3a3c;
    --rule: #8d8d92;
  }
  * { box-sizing: border-box; margin: 0; padding: 0; }
  html, body {
    width: 1200px; height: 1023px; overflow: hidden;
    background: var(--stage);
    font-family: "Open Sans", sans-serif;
  }
  .card {
    position: absolute; left: 250px; width: 700px; height: 400px;
    overflow: hidden; border-radius: 4px;
    box-shadow: 0 10px 30px rgba(0,0,0,.25);
  }
  /* Front */
  .card-front { top: 70px; }
  .front-top {
    position: absolute; inset: 0 0 150px 0;
    background: linear-gradient(160deg, var(--ink-mid) 0%, var(--ink-dark) 70%);
  }
  .brand {
    position: absolute; left: 48px; top: 48px;
    display: flex; align-items: center; gap: 14px;
  }
  .brand-dot {
    width: 26px; height: 26px; border-radius: 50%;
    background: var(--brand-blue);
  }
  .brand-name {
    font-weight: 700; font-size: 54px; line-height: 1;
    color: var(--brand-blue); letter-spacing: -1px;
  }
  .tagline {
    position: absolute; left: 90px; top: 112px;
    color: var(--text-light); font-size: 16px;
  }
  .rule {
    position: absolute; left: 40px; top: 214px;
    width: 400px; height: 1px; background: var(--rule);
  }
  .rule-top {
    position: absolute; right: 40px; top: 140px;
    width: 200px; height: 1px; background: var(--rule);
  }
  .person {
    position: absolute; right: 50px; top: 156px; text-align: right;
    color: var(--text-light);
  }
  .person-name { font-size: 32px; font-weight: 600; line-height: 1.1; }
  .person-title { font-size: 15px; }
  .contact-strip {
    position: absolute; left: 0; right: 0; top: 250px; height: 58px;
    background: var(--band-light);
    display: flex; align-items: center; justify-content: space-between;
    padding: 0 40px;
    color: var(--text-dark); font-size: 16px;
  }
  .contact-item { display: flex; align-items: center; gap: 10px; }
  .contact-item svg { width: 18px; height: 18px; fill: var(--text-dark); }
  .address-band {
    position: absolute; left: 0; right: 0; bottom: 0; height: 92px;
    background: linear-gradient(90deg, var(--blue-bright), var(--blue-deep));
    color: var(--text-light); font-size: 17px;
    display: flex; align-items: center; padding-left: 40px;
  }
  .notch {
    position: absolute; left: 335px; top: 307px;
    width: 0; height: 0;
    border-left: 11px solid transparent; border-right: 11px solid transparent;
    border-top: 11px solid var(--band-light);
  }
  /* Back */
  .card-back {
    top: 553px;
    background: radial-gradient(circle at 40% 60%, #4a9fdc 0%, #2f80c6 50%, var(--blue-deep) 100%);
  }
  .side-band {
    position: absolute; left: 62px; top: 0; bottom: 0; width: 48px;
    background: #1f2023;
    display: flex; align-items: center; justify-content: center;
  }
  .side-band span {
    transform: rotate(90deg); white-space: nowrap;
    color: var(--text-light); font-size: 14px;
  }
  .back-brand {
    position: absolute; left: 210px; top: 150px;
    display: flex; align-items: center; gap: 16px;
  }
  .back-brand .brand-dot { background: var(--text-light); width: 30px; height: 30px; }
  .back-brand .brand-name { color: var(--text-light); font-size: 68px; }
  .back-tagline {
    position: absolute; left: 262px; top: 236px;
    color: var(--text-light); font-size: 18px;
  }
</style>
</head>
<body>
  <section class="card card-front">
    <div class="front-top">
      <div class="brand">
        <span class="brand-dot"></span>
        <span class="brand-name">brightvale</span>
      </div>
      <p class="tagline">Commerce Advancing Methods</p>
      <span class="rule-top"></span>
      <div class="person">
        <p class="person-name">Martin Coles</p>
        <p class="person-title">Senior Partner</p>
      </div>
      <span class="rule"></span>
    </div>
    <div class="contact-strip">
      <span class="contact-item">
        <svg viewBox="0 0 24 24"><path d="M6.6 10.8a15 15 0 0 0 6.6 6.6l2.2-2.2c.3-.3.7-.4 1-.2 1.1.4 2.3.6 3.6.6.6 0 1 .4 1 1V20c0 .6-.4 1-1 1A17 17 0 0 1 3 4c0-.6.4-1 1-1h3.5c.6 0 1 .4 1 1 0 1.3.2 2.5.6 3.6.1.3 0 .7-.2 1z"/></svg>
        1 877 555 0143
      </span>
      <span class="contact-item">
        <svg viewBox="0 0 24 24"><path d="M7 2h10a2 2 0 0 1 2 2v16a2 2 0 0 1-2 2H7a2 2 0 0 1-2-2V4a2 2 0 0 1 2-2zm0 3v13h10V5zm5 14.2a1 1 0 1 0 0 1.6 1 1 0 0 0 0-1.6z"/></svg>
        1 519 555 0172
      </span>
      <span class="contact-item">
        <svg viewBox="0 0 24 24"><path d="M3 4h18a1 1 0 0 1 1 1v11a1 1 0 0 1-1 1h-7v2h3v2H7v-2h3v-2H3a1 1 0 0 1-1-1V5a1 1 0 0 1 1-1zm1 2v9h16V6z"/></svg>
        www.brightvale.example
      </span>
    </div>
    <span class="notch"></span>
    <div class="address-band">48 Harlow Avenue, Suite 610, Kingsford, Ontario, K7P 2B9</div>
  </section>

  <section class="card card-back">
    <div class="side-band"><span>www.brightvale.example</span></div>
    <div class="back-brand">
      <span class="brand-dot"></span>
      <span class="brand-name">brightvale</span>
    </div>
    <p class="back-tagline">Commerce Advancing Methods</p>
  </section>
</body>
</html>
```